Printing Company needs Website

PLEASE REVIEW ALL IMAGES, I HAVE INCLUDED A WEBSITE MOCKUP IDEA AND LOGO FILES IN THESE IMAGES.

Vel-Marks Provides printing services to multiple businesses. We Focus on 4 main markets. Signage (Signs, Banners, Wraps, Custom graphics), Printing (flyers, brochures, business cards, Postcards), Apparel (printed shirts, hoodies, sweatshirts), Promotional Products (mugs, golf balls, brava cans, pens), We try to sell ourselves on total brand imaging, our slogan is "Mark Everything." because we want to be able to provide any type of printing to our customers. Consumer targeting should be targeted towards small business, and wholesale targeting should be geared toward, merchandising, branding, marketing, design, signage, apparel, embroidery, and printing groups. WE DO OFFER DESIGN SERVICES, I have attached one orlwick guild logo design as an example.

I need a website designed both for wholesale and consumer based people. Wholesale customers would have their own login and consumers would also have their own.
I need there to be an online designer software (possibly java) built in so that the customer can order their product or upload their artwork online to see the proof for approval. There will need to be an commence setup, and I do have a quillpay account if that helps. Shipping must be auto calculated at the time of ordering. I would Like to make it to where when customer orders a product if it is outside of the dimensions requested on the site that the customer is warned of clipping or skewing.

I will be working closely aside the designer I pick to aid in the uploading and configuration of pricing structure, weight, and imagery if selected. This will be a lengthy project, and I will be willing to pay for the additional help so long as you are completely aware of the needs, Happy designing!!
Updates

I love all of the designs so far everyone! I will be reviewing PLEASE NOTE, IF I APPROVE YOUR WEB DESIGN, I WILL WANT YOU TO COMPLETE THE ENTIRE DESIGN INCLUDING A DESIGN PROOFING SETUP FOR MY CUSTOMERS INTEGRATED IN AS I HAVE STATED IN THE ORIGINAL STATEMENT. PLEASE ASK QUESTIONS IF YOU DON'T UNDERSTAND!

Target Market(s)

Small Business, School Athletics, Merchandising groups, Branding Groups, Larger Printers, Sign makers, Embroidery shops, Screen Printing Shops

Industry/Entity Type

It Company

Font styles to use
Sans Serif

Colors
000000
1b1b1b
757575
ec1f27

Requirements
Must have
• Built in design setup to each product with sizing, Ability to add pre-designed templates, .pdf print ready files after upload, Wholesale account, or Business accounts all with different pricing structures, Must be willing to aid in setup of all products and services (willing pay additional for setup costs.)
Nice to have
• SEO Optimization, targeting specific groups listed, automatic ordering to outsource vendors straight from site listing drop ship location if need be.

```html
<!DOCTYPE html>
<html lang="en">
<head>
<meta charset="utf-8">
<title>Vel-Marks — Mark Everything.</title>
<link rel="stylesheet" href="https://fonts.googleapis.com/css2?family=Lato:wght@700;900&family=Mulish:wght@400;500&family=Open+Sans:wght@400;600&family=Montserrat:wght@500;800&display=swap">
<style>
:root{
  --black:#000000;
  --panel:#1b1b1b;
  --grey:#757575;
  --red:#ec1f27;
  --red-dark:#c5161d;
  --white:#ffffff;
  --light:#d8d8d8;
  --purple:#8e1f8f;
  --blue:#5cb6d6;
  --yellow:#f4e100;
  --ring-red:#e4151d;
}
*{margin:0;padding:0;box-sizing:border-box}
html,body{width:1044px;height:1200px;overflow:hidden;background:var(--black)}
body{position:relative;font-family:"Open Sans",sans-serif;color:var(--white)}
.site-header{position:absolute;left:0;top:0;width:1044px;height:102px;background:var(--black)}
.brand-disc{position:absolute;left:452px;top:4px;width:140px;height:118px;border-radius:50%;background:var(--black);z-index:3}
.brand{position:absolute;left:0;top:26px;width:1044px;text-align:center;z-index:4}
.brand-name{font-family:"Montserrat",sans-serif;font-weight:800;font-size:40px;letter-spacing:1px;color:var(--white);line-height:44px}
.brand-tag{font-family:"Open Sans",sans-serif;font-size:12px;color:var(--white);margin-left:130px;line-height:16px}
.main-nav{position:absolute;left:0;top:102px;width:1044px;height:47px;background:var(--red);z-index:2}
.main-nav a{position:absolute;top:0;height:47px;line-height:47px;font-family:"Mulish",sans-serif;font-weight:500;font-size:15px;color:var(--white);text-decoration:none;padding:0 13px}
.main-nav a.sep{border-left:1px solid rgba(255,255,255,.35)}
.main-nav a.current{background:var(--red-dark);padding:0 22px}
.hero{position:absolute;left:0;top:149px;width:1044px;height:433px}
.hero-photo{position:absolute;inset:0;background:linear-gradient(180deg,#4d7bc0 0%,#8fb0d8 35%,#a9a49a 55%,#5e5e5e 75%,#8a8478 100%)}
.hero-title{position:absolute;left:106px;top:204px;font-family:"Lato",sans-serif;font-weight:900;font-size:49px;letter-spacing:1px;line-height:52px}
.hero-sub{position:absolute;left:106px;top:260px;font-family:"Lato",sans-serif;font-weight:700;font-size:25px;line-height:28px}
.slider-dots{position:absolute;left:492px;top:403px;display:flex;gap:8px}
.slider-dots span{width:12px;height:12px;border-radius:50%;background:var(--white)}
.slider-dots span.active{background:transparent;border:2px solid var(--white)}
.services{position:absolute;left:0;top:582px;width:1044px;height:319px;background:var(--panel)}
.service{position:absolute;top:30px;width:212px;text-align:center}
.service svg{display:block;margin:0 auto}
.service h3{font-family:"Open Sans",sans-serif;font-weight:400;font-size:19px;margin-top:14px;letter-spacing:.3px}
.service p{font-size:12px;line-height:16px;color:var(--grey);margin-top:5px;padding:0 14px}
.site-footer{position:absolute;left:0;top:901px;width:1044px;height:299px;background:var(--black)}
.footer-brand{position:absolute;left:112px;top:72px}
.footer-brand .brand-name{font-size:29px;line-height:32px}
.footer-brand .brand-tag{font-size:10px;margin-left:118px}
.footer-col{position:absolute;top:44px}
.footer-col h4{font-family:"Montserrat",sans-serif;font-weight:500;font-size:15px;letter-spacing:.3px;margin-bottom:14px}
.footer-col li{list-style:none;font-size:12px;line-height:25px;color:var(--white)}
.social li{display:flex;align-items:center;gap:9px;line-height:31px}
.social i{display:inline-block;width:22px;height:22px;border-radius:50%}
.footer-rule{position:absolute;left:104px;top:236px;width:836px;height:1px;background:#333}
.copyright{position:absolute;left:0;top:253px;width:1044px;text-align:center;padding-right:30px;font-size:11.5px;color:var(--grey)}
</style>
</head>
<body>
<header class="site-header">
  <div class="brand-disc"></div>
  <div class="brand">
    <div class="brand-name">VEL-MARKS</div>
    <div class="brand-tag">Mark Everything.</div>
  </div>
</header>
<nav class="main-nav">
  <a class="current" style="left:104px">Home</a>
  <a style="left:185px">Signage</a>
  <a class="sep" style="left:267px">Printing</a>
  <a class="sep" style="left:342px">Design</a>
  <a style="left:551px">Promotional</a>
  <a class="sep" style="left:660px">Apparel</a>
  <a class="sep" style="left:739px">About Us</a>
  <a class="sep" style="left:829px">Contact Us</a>
</nav>
<section class="hero">
  <div class="hero-photo" role="img" aria-label="Photo of a roadside restaurant building with large printed window wraps, parked cars and landscaping under a blue sky"></div>
  <h1 class="hero-title">MARK EVERYTHING</h1>
  <p class="hero-sub">MAURIS VEL LACUS VITAE</p>
  <div class="slider-dots"><span class="active"></span><span></span><span></span><span></span></div>
</section>
<section class="services">
  <div class="service" style="left:98px">
    <svg width="170" height="155" viewBox="0 0 170 155"><ellipse cx="85" cy="78" rx="81" ry="74" fill="var(--purple)" transform="rotate(-18 85 78)"/><ellipse cx="82" cy="84" rx="60" ry="55" fill="var(--black)" transform="rotate(-18 82 84)"/>
      <g fill="none" stroke="var(--white)" stroke-width="3"><line x1="61" y1="52" x2="105" y2="52"/><path d="M67 52v52l16-12 16 12V52"/><path d="M80 68v16M86 68v16M76 76h14"/></g></svg>
    <h3>Signage</h3><p>Signs, Banners, Wraps, Custom graphics</p>
  </div>
  <div class="service" style="left:311px">
    <svg width="170" height="155" viewBox="0 0 170 155"><ellipse cx="85" cy="78" rx="81" ry="74" fill="var(--blue)" transform="rotate(-18 85 78)"/><ellipse cx="82" cy="84" rx="60" ry="55" fill="var(--black)" transform="rotate(-18 82 84)"/>
      <g fill="none" stroke="var(--white)" stroke-width="3"><rect x="67" y="56" width="32" height="12"/><rect x="56" y="68" width="54" height="22" rx="3"/><path d="M64 90l-4 14h46l-4-14M66 97h34"/></g></svg>
    <h3>Printing</h3><p>flyers, brochures, business cards, Postcards</p>
  </div>
  <div class="service" style="left:523px">
    <svg width="170" height="155" viewBox="0 0 170 155"><ellipse cx="85" cy="78" rx="81" ry="74" fill="var(--yellow)" transform="rotate(-18 85 78)"/><ellipse cx="82" cy="84" rx="60" ry="55" fill="var(--black)" transform="rotate(-18 82 84)"/>
      <path d="M72 52l-18 10 6 14 8-4v34h32V72l8 4 6-14-18-10c-2 6-7 9-12 9s-10-3-12-9z" fill="none" stroke="var(--white)" stroke-width="2.5"/></svg>
    <h3>Apparel</h3><p>Printed shirts, hoodies, sweatshirts</p>
  </div>
  <div class="service" style="left:736px">
    <svg width="170" height="155" viewBox="0 0 170 155"><ellipse cx="85" cy="78" rx="81" ry="74" fill="var(--ring-red)" transform="rotate(-18 85 78)"/><ellipse cx="82" cy="84" rx="60" ry="55" fill="var(--black)" transform="rotate(-18 82 84)"/>
      <g fill="none" stroke="var(--white)" stroke-width="3"><path d="M64 60h36v12c0 12-8 18-18 18s-18-6-18-18z"/><path d="M100 64c8 0 8 12-2 12"/><path d="M54 96h56M60 101h44"/></g></svg>
    <h3 style="white-space:nowrap;margin-left:-20px;margin-right:-20px">Promotional Products</h3><p>Mugs, golf balls, brava cans, pens</p>
  </div>
</section>
<footer class="site-footer">
  <div class="footer-brand">
    <div class="brand-name">VEL-MARKS</div>
    <div class="brand-tag">Mark Everything.</div>
  </div>
  <div class="footer-col" style="left:326px"><h4>COMPANY</h4><ul><li>Home</li><li>Signage</li><li>Printing</li><li>Design</li></ul></div>
  <div class="footer-col" style="left:457px"><h4>SUBLINKS</h4><ul><li>Promotional</li><li>Apparel</li><li>About Us</li><li>Contact Us</li></ul></div>
  <div class="footer-col" style="left:595px;top:46px"><h4>CONTACT US</h4><ul><li>410 Harlow Commons Suite B12</li><li>Orlwick, PA 19990</li><li>(555) 014-2200</li><li>info@velmarks.example</li></ul></div>
  <div class="footer-col social" style="left:816px"><h4 style="margin-bottom:8px">FOLLOW US</h4><ul>
    <li><i style="background:#2f5aa0"></i>Friendwall</li>
    <li><i style="background:#2ea8e0"></i>Chirper</li>
    <li><i style="background:#1b6e9e"></i>Workring</li>
    <li><i style="background:#d8462e"></i>Circlenet</li>
  </ul></div>
  <div class="footer-rule"></div>
  <p class="copyright">© 2016 Company Name &nbsp;All right reserved &nbsp;Term of Use</p>
</footer>
</body>
</html>
```